Design a Mobile App for Landscape Businesses

This project is to design the first three screens for a mobile app for Landscape and Lawncare businesses. This app will serve as a directory for homeowners to locate landscape and lawn care businesses and for landscape businesses and contractors to run their business. See the attached PDF for more information and example
Here is the link to the description https://lnkbrev.example/q7z3Kp

Target Market(s)

Landscape and lawn care business, gardeners, home owners

Industry/Entity Type

Landscape Gardening

Logo Text

Verdalink

Colors

Designer to choose colors to be used in the design.

```html
<!DOCTYPE html>
<html lang="en">
<head>
<meta charset="utf-8">
<title>Verdalink – Sign up</title>
<link href="https://fonts.googleapis.com/css2?family=Montserrat:wght@400;500;600;700&display=swap" rel="stylesheet">
<style>
  :root {
    --photo-top: #7d8f86;
    --photo-mid: #5f7a6a;
    --photo-low: #6b6a7c;
    --photo-bottom: #4d5a4f;
    --white: #ffffff;
    --ink: #2b2b2b;
    --accent: #2fb6d6;
    --social-a-start: #2b6cbf;
    --social-a-end: #2c95d4;
    --social-b-start: #27a6d9;
    --social-b-end: #26c6d6;
    --email-start: #33b6d9;
    --email-end: #4fe0a6;
    --divider: rgba(255,255,255,0.55);
  }
  * { box-sizing: border-box; margin: 0; padding: 0; }
  html, body { width: 675px; height: 1200px; overflow: hidden; }
  body { font-family: "Montserrat", sans-serif; color: var(--white); }
  .screen { position: relative; width: 675px; height: 1200px; overflow: hidden; }
  .backdrop {
    position: absolute; inset: 0;
    background:
      radial-gradient(ellipse 60% 40% at 70% 45%, rgba(190,200,195,0.45), transparent 70%),
      linear-gradient(180deg, var(--photo-top) 0%, var(--photo-mid) 40%, var(--photo-low) 75%, var(--photo-bottom) 100%);
  }
  .status-bar {
    position: absolute; top: 0; left: 0; right: 0; height: 43px;
    display: flex; justify-content: flex-end; align-items: center; gap: 10px;
    padding-right: 18px; font-size: 20px; font-weight: 500;
  }
  .brand { position: absolute; top: 140px; left: 0; right: 0; text-align: center; }
  .brand-mark {
    width: 78px; height: 78px; border-radius: 50%;
    border: 4px solid var(--white); margin: 0 auto 30px;
  }
  .brand-name { font-size: 40px; font-weight: 700; line-height: 1; }
  .brand-sub { margin-top: 14px; font-size: 21px; letter-spacing: 14px; padding-left: 14px; font-weight: 500; }
  .tagline { position: absolute; top: 352px; width: 100%; text-align: center; font-size: 30px; font-weight: 500; }
  .login-prompt { position: absolute; top: 468px; width: 100%; text-align: center; font-size: 23px; }
  .login-prompt b { font-weight: 700; }
  .btn {
    position: absolute; left: 22px; width: 633px; height: 82px; border-radius: 41px;
    display: flex; align-items: center; justify-content: center; gap: 16px;
    font-size: 23px; font-weight: 700; color: var(--white);
  }
  .btn-facepage { top: 583px; background: linear-gradient(90deg, var(--social-a-start), var(--social-a-end)); }
  .btn-chirper { top: 682px; background: linear-gradient(90deg, var(--social-b-start), var(--social-b-end)); }
  .btn-email { top: 1080px; background: linear-gradient(90deg, var(--email-start), var(--email-end)); }
  .btn-dot { width: 30px; height: 30px; border-radius: 50%; background: var(--white); }
  .divider { position: absolute; top: 811px; left: 27px; width: 617px; height: 2px; background: var(--divider); }
  .field {
    position: absolute; left: 29px; width: 619px; height: 83px; background: var(--white);
    border-radius: 4px; display: flex; align-items: center; gap: 18px; padding-left: 26px;
    font-size: 24px; color: var(--ink);
  }
  .field-email { top: 853px; }
  .field-password { top: 958px; }
</style>
</head>
<body>
<main class="screen">
  <div class="backdrop" role="img" aria-label="Photo of a gardener watering flowers with a watering can"></div>

  <div class="status-bar">
    <svg width="22" height="22" viewBox="0 0 22 22" fill="none" stroke="#fff" stroke-width="2"><circle cx="11" cy="12" r="8"/><path d="M11 8v4l3 2"/></svg>
    <svg width="24" height="20" viewBox="0 0 24 20"><path d="M12 19L0 5a18 18 0 0 1 24 0z" fill="#fff"/></svg>
    <svg width="20" height="20" viewBox="0 0 20 20"><path d="M20 0v20H0z" fill="#fff"/></svg>
    <svg width="13" height="22" viewBox="0 0 13 22"><rect x="0" y="3" width="13" height="19" rx="1.5" fill="#fff"/><rect x="4" y="0" width="5" height="3" fill="#fff"/></svg>
    <span>16:54</span>
  </div>

  <header class="brand">
    <div class="brand-mark"></div>
    <h1 class="brand-name">Verdalink</h1>
    <p class="brand-sub">LOGO TBC</p>
  </header>

  <p class="tagline">On demand gardening services</p>
  <p class="login-prompt">Already have an account? <b>Log in</b></p>

  <a class="btn btn-facepage"><span class="btn-dot"></span>Sign up with Facepage</a>
  <a class="btn btn-chirper"><span class="btn-dot"></span>Sign up with Chirper</a>

  <div class="divider"></div>

  <label class="field field-email">
    <svg width="28" height="20" viewBox="0 0 28 20" fill="none" stroke="var(--accent)" stroke-width="2.4"><rect x="1.5" y="1.5" width="25" height="17" rx="1"/><path d="M1.5 2l12.5 10L26.5 2"/></svg>
    Email address
  </label>
  <label class="field field-password">
    <svg width="22" height="28" viewBox="0 0 22 28"><path d="M5 12V8a6 6 0 0 1 12 0v4" fill="none" stroke="var(--accent)" stroke-width="3"/><rect x="1" y="12" width="20" height="15" rx="2" fill="var(--accent)"/></svg>
    Password
  </label>

  <a class="btn btn-email">Sign up with Email address</a>
</main>
</body>
</html>
```